Investment Management Firm Power point template

Marrow Holdings is a real estate investment firm focused on buying commercial office and residential property in the UK. We produce powerpoint presentations for our Board of Directors, Investment Committee and also to external investors.

We are looking for a powerpoint design template which we can use for future presentations which provide a professional look and feel.

Our current website: http://www.marrowholdings.example.co.uk/

Target Market(s)

Institution Investors, Board of Directors, Professionals

Industry/Entity Type

Real Estate

Requirements
Must have
• Leverage off the current logo and colour scheme. However, does not have to purely rely on this colour scheme.
• - Title page
• - Content Page
• - Slide where graphs can be incorporated
• - Slide where photos can be incorporated
• - Slide of UK Map which can show where the property portfolio is currently located
• - Other slides incorporating smart art or other designs that can be used for future presentations
Nice to have
• An example of graphics that we would love to have in the powerpoint pack which we can easily edit has been attached

```html
<!DOCTYPE html>
<html lang="en">
<head>
<meta charset="utf-8">
<title>Marrow Holdings – Content Slide</title>
<link rel="stylesheet" href="https://fonts.googleapis.com/css2?family=Titillium+Web:ital,wght@0,400;0,600;0,700;1,600&display=swap">
<style>
  :root {
    --brand-blue: #1c4f7f;
    --band-blue: #2b6a96;
    --ink: #222222;
    --body-ink: #333333;
    --paper: #ffffff;
    --photo-light: #d9d6cf;
    --photo-mid: #a8a39a;
    --photo-dark: #5a564f;
  }
  html, body {
    margin: 0;
    padding: 0;
    width: 1200px;
    height: 900px;
    overflow: hidden;
    background: var(--paper);
  }
  .slide {
    position: relative;
    width: 1200px;
    height: 900px;
    background: var(--paper);
    font-family: "Titillium Web", Arial, sans-serif;
    overflow: hidden;
  }
  .slide-title {
    position: absolute;
    left: 36px;
    top: 22px;
    margin: 0;
    font-size: 37px;
    font-weight: 700;
    color: var(--brand-blue);
    line-height: 1.1;
  }
  .title-rule {
    position: absolute;
    left: 0;
    top: 72px;
    width: 290px;
    height: 3px;
    background: var(--brand-blue);
  }
  .content {
    position: absolute;
    left: 66px;
    top: 160px;
    width: 450px;
  }
  .subheading {
    margin: 0 0 12px;
    font-size: 25px;
    font-weight: 600;
    color: var(--ink);
    line-height: 1.3;
  }
  .body-copy {
    margin: 0;
    font-size: 19.5px;
    line-height: 33px;
    color: var(--body-ink);
  }
  .callout {
    margin: 30px 0 32px;
    font-size: 22px;
    font-weight: 600;
    font-style: italic;
    line-height: 33px;
    color: var(--brand-blue);
  }
  .photo-area {
    position: absolute;
    left: 600px;
    top: 0;
    width: 600px;
    height: 837px;
    background: linear-gradient(150deg, var(--photo-mid) 0%, var(--photo-light) 40%, #c8c4bb 65%, var(--photo-dark) 100%);
  }
  .footer-band {
    position: absolute;
    left: 0;
    top: 840px;
    width: 1200px;
    height: 60px;
    background: var(--band-blue);
  }
  .brand-box {
    position: absolute;
    left: 912px;
    top: 843px;
    width: 280px;
    height: 52px;
    background: var(--paper);
    display: flex;
    align-items: center;
    gap: 14px;
    padding-left: 16px;
    box-sizing: border-box;
  }
  .brand-square {
    width: 26px;
    height: 26px;
    border: 2px solid var(--brand-blue);
    box-sizing: border-box;
  }
  .brand-name {
    font-size: 25px;
    font-weight: 600;
    color: var(--brand-blue);
    white-space: nowrap;
  }
</style>
</head>
<body>
  <main class="slide">
    <h1 class="slide-title">Slide Title Here</h1>
    <div class="title-rule"></div>

    <section class="content">
      <h2 class="subheading">Subtext Heading Here</h2>
      <p class="body-copy">While a property’s fundamentals are important to us, we put equal focus on the people who use and enjoy our spaces. The experience of being in our buildings — from design to atmosphere — is strategically planned. Functionality and efficiency are crucial and technology is in our DNA.</p>
      <p class="callout">With these fundamental characteristics in mind we strive to create businesses around our properties</p>
      <p class="body-copy">As part of the Ashcombe Partners Group we directly and indirectly benefit from the ecosystem of companies around us. Ashcombe Partners brings unrivalled expertise in building successful, long-lasting businesses.</p>
    </section>

    <div class="photo-area" role="img" aria-label="Photo of a bright loft apartment interior with tall windows, a potted plant and a modern kitchen"></div>

    <footer class="footer-band"></footer>
    <div class="brand-box">
      <span class="brand-square"></span>
      <span class="brand-name">Marrow Holdings</span>
    </div>
  </main>
</body>
</html>
```